Business Card for Fashion House

We need a business card design for our personalize fashion service for our customers. the business card should reflect reliability, luxury and creativity.
The brand Gravetto is extracted from "Graceful Velvetto"; Gravetto provides fashion designs sprinkled with luxury and style tailored for our elite clients character profile.
Gravetto is created for those who embody class and elegance with a passion for style.
Target Market(s)
Affluent Customers
Industry/Entity Type
Fashion
Contact Information for Business Card
Samira Haddadin
Fashion Designer
Telephone: +971 4 555 0192
Mobile +971 50 555 0147
Emal info@gravetto-example.com
Website www.gravetto-example.com
Social Media Youtube g+ Facebook Instagram Pin /gravetto
Font styles to use
Other font styles liked:
- Audrey provided
Look and feel
Each slider illustrates characteristics of the customer's brand and the style your logo design should communicate.

```html
<!DOCTYPE html>
<html lang="en">
<head>
<meta charset="utf-8">
<title>Gravetto — Business Card</title>
<link rel="stylesheet" href="https://fonts.googleapis.com/css2?family=Marcellus&family=Cormorant+Garamond:wght@500;600&family=Montserrat:wght@400;600&display=swap">
<style>
  :root {
    --backdrop: #e9e6e3;
    --card-dark: #3a3331;
    --card-light: #f1f1f1;
    --ink-dark: #2f2927;
    --ink-light: #ffffff;
    --ink-muted: #d8d2cf;
    --card-radius: 22px;
  }
  * { box-sizing: border-box; margin: 0; padding: 0; }
  html, body { width: 1200px; height: 1000px; overflow: hidden; }
  body {
    background: var(--backdrop);
    font-family: "Cormorant Garamond", Georgia, serif;
    display: flex;
    flex-direction: column;
    align-items: center;
    justify-content: center;
    gap: 60px;
  }
  .card {
    width: 700px;
    height: 400px;
    border-radius: var(--card-radius);
    overflow: hidden;
    position: relative;
    box-shadow: 0 10px 28px rgba(0,0,0,.18);
  }

  /* Front */
  .card-front { background: var(--card-dark); color: var(--ink-light); }
  .front-top {
    height: 175px;
    background: var(--card-light);
    display: flex;
    flex-direction: column;
    align-items: center;
    justify-content: center;
    gap: 14px;
  }
  .brand-mark { display: flex; align-items: center; gap: 16px; }
  .brand-dot { width: 14px; height: 14px; border-radius: 50%; background: var(--ink-dark); }
  .brand-name {
    font-family: "Marcellus", Georgia, serif;
    font-size: 34px;
    letter-spacing: 12px;
    color: var(--ink-dark);
    text-transform: uppercase;
  }
  .front-bottom {
    display: flex;
    justify-content: center;
    gap: 70px;
    padding: 34px 40px 0;
  }
  .person-name {
    font-family: "Montserrat", Arial, sans-serif;
    font-weight: 600;
    font-size: 21px;
    text-transform: uppercase;
    letter-spacing: .5px;
  }
  .person-title { font-size: 16px; color: var(--ink-muted); margin: 2px 0 14px 60px; }
  .contact-list, .social-list { list-style: none; }
  .contact-list li, .social-list li {
    display: flex;
    align-items: center;
    gap: 10px;
    font-size: 17px;
    line-height: 27px;
    letter-spacing: .5px;
  }
  .contact-list svg { width: 15px; height: 15px; flex: none; }
  .social-dot { width: 11px; height: 11px; border-radius: 50%; background: var(--ink-light); flex: none; }

  /* Back */
  .card-back {
    background: var(--card-dark);
    color: var(--ink-light);
    display: flex;
    flex-direction: column;
    align-items: center;
    justify-content: center;
    gap: 34px;
  }
  .card-back .brand-dot { background: var(--ink-light); width: 18px; height: 18px; }
  .card-back .brand-name { color: var(--ink-light); font-size: 52px; letter-spacing: 18px; }
  .back-web {
    font-family: "Montserrat", Arial, sans-serif;
    font-size: 17px;
    color: var(--ink-muted);
  }
  .back-web strong { color: var(--ink-light); font-weight: 600; }
</style>
</head>
<body>

<section class="card card-front">
  <div class="front-top">
    <div class="brand-mark">
      <span class="brand-dot"></span>
      <span class="brand-name">Gravetto</span>
    </div>
  </div>
  <div class="front-bottom">
    <div class="person">
      <h1 class="person-name">Samira Haddadin</h1>
      <p class="person-title">Fashion Designer</p>
      <ul class="contact-list">
        <li>
          <svg viewBox="0 0 16 16" fill="none" stroke="#fff" stroke-width="1.6"><path d="M3 2h3l1.5 3.5-2 1.2a8 8 0 0 0 3.8 3.8l1.2-2L14 10v3a1 1 0 0 1-1 1A11 11 0 0 1 2 3a1 1 0 0 1 1-1z"/></svg>
          +971 4 555 0192
        </li>
        <li>
          <svg viewBox="0 0 16 16" fill="none" stroke="#fff" stroke-width="1.6"><rect x="4.5" y="1.5" width="7" height="13" rx="1.5"/><line x1="7" y1="12" x2="9" y2="12"/></svg>
          +971 50 555 0147
        </li>
        <li>
          <svg viewBox="0 0 16 16" fill="none" stroke="#fff" stroke-width="1.4"><circle cx="8" cy="8" r="6.3"/><ellipse cx="8" cy="8" rx="2.8" ry="6.3"/><line x1="1.7" y1="8" x2="14.3" y2="8"/></svg>
          www.gravetto-example.com
        </li>
        <li>
          <svg viewBox="0 0 16 16" fill="none" stroke="#fff" stroke-width="1.5"><rect x="1.5" y="3.5" width="13" height="9" rx="1"/><path d="M1.5 4l6.5 5 6.5-5"/></svg>
          info@gravetto-example.com
        </li>
      </ul>
    </div>
    <ul class="social-list">
      <li><span class="social-dot"></span>/gravetto</li>
      <li><span class="social-dot"></span>/gravetto</li>
      <li><span class="social-dot"></span>/gravetto</li>
      <li><span class="social-dot"></span>/gravetto</li>
      <li><span class="social-dot"></span>/gravetto</li>
    </ul>
  </div>
</section>

<section class="card card-back">
  <div class="brand-mark">
    <span class="brand-dot"></span>
    <span class="brand-name">Gravetto</span>
  </div>
  <p class="back-web">www.<strong>gravetto-example</strong>.com</p>
</section>

</body>
</html>
```